Business Card for Field Lotus-Eco Friendly Organic Clothing Brand

We are looking for an amazing business card for our eco friendly, organic clothing brand. We are thinking maybe a business card with a peel off sticker on the back, since our hanging clothing tag is a peel off sticker on the back. I will attach our hang tag so we can make sure we stay in line with our design. I've also attached a bag we are doing because I do like the scattered emblem look as well.

```html
<!DOCTYPE html>
<html lang="en">
<head>
<meta charset="utf-8">
<title>Field Lotus – Business Card</title>
<link rel="stylesheet" href="https://fonts.googleapis.com/css2?family=Open+Sans:wght@400;600;700&display=swap">
<style>
  :root {
    --backdrop: #8e8e8e;
    --card-white: #ebebee;
    --card-black: #121212;
    --camo-dark: #1f2418;
    --camo-olive: #343b26;
    --gold: #c9a94a;
    --gold-light: #ecd58a;
    --ink: #1c1c1c;
    --ink-soft: #3a3a3a;
    --on-dark: #f2f2f2;
  }
  * { box-sizing: border-box; margin: 0; padding: 0; }
  html, body {
    width: 1105px; height: 1200px; overflow: hidden;
    background: var(--backdrop);
    font-family: "Open Sans", Arial, sans-serif;
  }
  .card {
    position: absolute; left: 182px; width: 747px; height: 426px; overflow: hidden;
  }
  .card-front { top: 119px; background: var(--card-white); }
  .card-back { top: 637px; background: var(--card-black); }
  .card-art { position: absolute; inset: 0; }

  .contact-list {
    position: absolute; left: 37px; top: 278px; list-style: none;
    color: var(--on-dark); font-size: 19px; line-height: 29px;
  }
  .contact-list li { display: flex; align-items: center; gap: 9px; }
  .contact-list .address { margin-bottom: 3px; }
  .contact-icon { width: 17px; height: 17px; flex: none; }

  .person {
    position: absolute; right: 33px; top: 335px; text-align: right; color: var(--ink);
  }
  .person-name { font-size: 26px; font-weight: 700; line-height: 32px; }
  .person-role { font-size: 20px; color: var(--ink-soft); line-height: 26px; }

  .brand-tag { position: absolute; }
  .brand-tag-front { left: 417px; top: 40px; width: 291px; height: 138px; }
  .brand-tag-back { left: 177px; top: 116px; width: 379px; height: 172px; }
  .brand-tag svg { position: absolute; inset: 0; width: 100%; height: 100%; }
  .brand-name, .brand-url {
    position: absolute; text-align: center; white-space: nowrap;
  }
  .brand-name { color: var(--gold); font-weight: 700; }
  .brand-url { color: var(--on-dark); }
  .brand-tag-front .brand-name { left: 106px; width: 170px; top: 40px; font-size: 22px; line-height: 30px; }
  .brand-tag-front .brand-url { left: 106px; width: 170px; top: 88px; font-size: 10px; line-height: 14px; }
  .brand-tag-back .brand-name { left: 140px; width: 222px; top: 56px; font-size: 29px; line-height: 38px; }
  .brand-tag-back .brand-url { left: 140px; width: 222px; top: 118px; font-size: 13px; line-height: 18px; }

  .social-row {
    position: absolute; top: 29px; right: 38px; display: flex; gap: 12px; list-style: none;
  }
  .social-dot {
    width: 42px; height: 42px; border-radius: 50%;
    border: 2px solid var(--on-dark); background: var(--card-black);
  }
</style>
</head>
<body>

<section class="card card-front" aria-label="Card front">
  <svg class="card-art" viewBox="0 0 747 426">
    <defs>
      <linearGradient id="camoTone" x1="0" y1="0" x2="1" y2="1">
        <stop offset="0" stop-color="#343b26"/>
        <stop offset="1" stop-color="#1f2418"/>
      </linearGradient>
      <linearGradient id="goldLine" x1="0" y1="0" x2="1" y2="1">
        <stop offset="0" stop-color="#ecd58a"/>
        <stop offset="1" stop-color="#c9a94a"/>
      </linearGradient>
    </defs>
    <polygon class="camo-diamond" role="img" aria-label="Dark olive camouflage pattern panel"
      points="0,246 170,80 460,363 397,426 0,426" fill="url(#camoTone)"/>
    <polyline class="gold-frame" points="0,299 184,115 426,357 357,426"
      fill="none" stroke="url(#goldLine)" stroke-width="5"/>
  </svg>

  <div class="brand-tag brand-tag-front">
    <svg viewBox="0 0 291 138">
      <rect x="22" y="11" width="269" height="117" rx="12" fill="var(--card-black)"/>
      <rect role="img" aria-label="Camouflage pattern inside brand tag" x="32" y="20" width="249" height="99" rx="6" fill="url(#camoTone)"/>
      <rect x="32" y="20" width="249" height="99" rx="6" fill="none" stroke="var(--gold)" stroke-width="2.5"/>
      <rect x="40" y="39" width="58" height="58" fill="var(--gold)"/>
    </svg>
    <span class="brand-name">FIELD LOTUS</span>
    <span class="brand-url">www.fieldlotus.com</span>
  </div>

  <ul class="contact-list">
    <li class="address">Harbor Point, FL&nbsp;&nbsp;33021</li>
    <li>
      <svg class="contact-icon" viewBox="0 0 24 24"><path fill="var(--gold)" d="M6.6 10.8a15.2 15.2 0 0 0 6.6 6.6l2.2-2.2a1 1 0 0 1 1-.25 11.4 11.4 0 0 0 3.6.57 1 1 0 0 1 1 1V20a1 1 0 0 1-1 1A17 17 0 0 1 3 4a1 1 0 0 1 1-1h3.5a1 1 0 0 1 1 1c0 1.25.2 2.45.57 3.57a1 1 0 0 1-.25 1z"/></svg>
      (877) 555-0142
    </li>
    <li>
      <svg class="contact-icon" viewBox="0 0 24 24"><path fill="var(--gold)" d="M6.6 10.8a15.2 15.2 0 0 0 6.6 6.6l2.2-2.2a1 1 0 0 1 1-.25 11.4 11.4 0 0 0 3.6.57 1 1 0 0 1 1 1V20a1 1 0 0 1-1 1A17 17 0 0 1 3 4a1 1 0 0 1 1-1h3.5a1 1 0 0 1 1 1c0 1.25.2 2.45.57 3.57a1 1 0 0 1-.25 1z"/></svg>
      (877) KINDNES
    </li>
    <li>
      <svg class="contact-icon" viewBox="0 0 24 24"><rect x="2" y="5" width="20" height="14" rx="1.5" fill="var(--gold)"/><path d="M3 6l9 7 9-7" fill="none" stroke="var(--camo-dark)" stroke-width="1.8"/></svg>
      hello@fieldlotus.com
    </li>
  </ul>

  <div class="person">
    <p class="person-name">Dana Reyes</p>
    <p class="person-role">CEO/Founder</p>
  </div>
</section>

<section class="card card-back" aria-label="Card back">
  <svg class="card-art" viewBox="0 0 747 426">
    <rect role="img" aria-label="Faint scattered pattern of peace, love and namaste words" width="747" height="426" fill="#161616"/>
  </svg>

  <ul class="social-row" aria-label="Social links">
    <li class="social-dot"></li>
    <li class="social-dot"></li>
    <li class="social-dot"></li>
    <li class="social-dot"></li>
  </ul>

  <div class="brand-tag brand-tag-back">
    <svg viewBox="0 0 379 172">
      <rect x="37" y="25" width="342" height="138" rx="14" fill="var(--card-black)"/>
      <rect role="img" aria-label="Camouflage pattern inside brand tag" x="48" y="35" width="320" height="118" rx="7" fill="url(#camoTone)"/>
      <rect x="48" y="35" width="320" height="118" rx="7" fill="none" stroke="var(--gold)" stroke-width="3"/>
      <rect x="56" y="55" width="76" height="76" fill="var(--gold)"/>
    </svg>
    <span class="brand-name">FIELD LOTUS</span>
    <span class="brand-url">www.fieldlotus.com</span>
  </div>
</section>

</body>
</html>
```